SOLVE Study flyer

I need help designing a flyer for a research study that will include brain imaging in adolescents. The info is in the attached document. The study is called the Sequoia Outlook Lantern Valley Echo (SOLVE) study. Ideally this would be returned as a document that I can edit in the future as we will have several new recruitment phases (different age groups, etc. I also would love to have a logo designed as part of this project, but I recognize that might be a separate design request.

```html
<!DOCTYPE html>
<html lang="en">
<head>
<meta charset="utf-8">
<title>SOLVE Study Flyer</title>
<link href="https://fonts.googleapis.com/css2?family=Poppins:ital,wght@0,400;0,500;0,600;0,700;0,800;1,500;1,600;1,700;1,800&display=swap" rel="stylesheet">
<style>
  :root {
    --purple: #5a1d5c;
    --purple-deep: #4a1249;
    --green: #1a7a4a;
    --mint: #4fc295;
    --ink: #2b2b2b;
    --paper: #ffffff;
    --backdrop: #ecebe8;
    --photo-a: #f6f4f2;
    --photo-b: #e9d3cf;
  }
  * { margin: 0; padding: 0; box-sizing: border-box; }
  html, body { width: 1200px; height: 1200px; overflow: hidden; }
  body { background: var(--backdrop); font-family: "Poppins", sans-serif; color: var(--ink); }

  .flyer {
    position: absolute; left: 150px; top: 25px;
    width: 900px; height: 1150px;
    background: var(--paper); overflow: hidden;
    box-shadow: 0 6px 24px rgba(0,0,0,.12);
  }
  .top-tab {
    position: absolute; left: 545px; top: 0; width: 355px; height: 25px;
    background: var(--mint); border-bottom-left-radius: 22px;
  }

  .brand { position: absolute; left: 28px; top: 30px; display: flex; align-items: center; gap: 16px; }
  .brand-dot { width: 126px; height: 126px; border-radius: 50%; background: var(--purple); }
  .brand-name { font-weight: 700; font-size: 38px; line-height: 1; color: var(--ink); letter-spacing: 1px; }
  .brand-name span { display: block; font-size: 21px; letter-spacing: 3px; margin-top: 4px; padding-left: 24px; }

  .headline {
    position: absolute; left: 30px; top: 172px; width: 460px;
    font-weight: 800; font-size: 35px; line-height: 41px; text-transform: uppercase; letter-spacing: -0.5px;
  }
  .headline .q1 { color: var(--purple); display: block; }
  .headline .q2 { color: var(--green); display: block; }

  .intro {
    position: absolute; left: 35px; top: 390px; width: 430px;
    font-size: 20px; line-height: 30px;
  }
  .intro b { font-weight: 800; font-style: italic; color: var(--ink); }

  .photo {
    position: absolute; left: 485px; top: 105px; width: 500px; height: 560px;
    border-radius: 50%;
    background: radial-gradient(circle at 55% 55%, var(--photo-b), var(--photo-a) 70%);
  }
  .arcs { position: absolute; left: 0; top: 0; }

  .involves {
    position: absolute; left: 40px; top: 565px; width: 440px; height: 437px;
    background: linear-gradient(180deg, var(--purple) 0%, var(--purple-deep) 100%);
    border-radius: 0 40px 0 70px; color: #fff; padding: 22px 18px 0 18px;
  }
  .involves h2 { font-size: 28px; font-weight: 700; line-height: 34px; }
  .involves h2 .rule { display: inline-block; width: 190px; height: 1px; background: rgba(255,255,255,.8); vertical-align: middle; margin-left: 6px; }
  .steps { list-style: none; margin-top: 16px; }
  .steps li { display: flex; gap: 16px; font-size: 17px; line-height: 25px; margin-bottom: 24px; }
  .steps svg { flex: none; margin-top: 2px; }

  .eligible { position: absolute; left: 560px; top: 695px; width: 320px; }
  .eligible h2 { color: var(--green); font-size: 28px; font-weight: 700; line-height: 33px; }
  .criteria { list-style: none; position: relative; margin-top: 22px; }
  .criteria::before { content: ""; position: absolute; left: 17px; top: 10px; bottom: 40px; width: 2px; background: var(--green); }
  .criteria li { position: relative; display: flex; gap: 14px; font-size: 17px; line-height: 25px; margin-bottom: 24px; }
  .criteria .dot { flex: none; width: 36px; height: 36px; border-radius: 50%; background: var(--green); display: flex; align-items: center; justify-content: center; }

  .contact { position: absolute; left: 45px; top: 1018px; }
  .contact p { font-style: italic; font-weight: 500; font-size: 20px; line-height: 28px; }
  .email {
    margin-top: 10px; display: inline-flex; align-items: center; gap: 8px;
    background: var(--green); color: #fff; border-radius: 20px; padding: 2px 18px 4px 12px;
    font-weight: 700; font-size: 27px;
  }

  .pay {
    position: absolute; left: 610px; top: 1030px; width: 272px; height: 82px;
    border: 2px solid var(--purple); border-radius: 40px;
    color: var(--purple); font-weight: 800; font-style: italic; font-size: 28px; line-height: 30px;
    text-align: right; padding: 8px 18px 0 0;
  }
</style>
</head>
<body>
<main class="flyer">
  <div class="top-tab"></div>

  <header class="brand">
    <div class="brand-dot"></div>
    <div class="brand-name">SOLVE<span>STUDY</span></div>
  </header>

  <div class="photo" role="img" aria-label="Smiling girl in a pink t-shirt pointing toward the headline"></div>
  <svg class="arcs" width="900" height="1150" viewBox="0 0 900 1150" aria-hidden="true">
    <path d="M640 95 Q720 60 800 65" fill="none" stroke="var(--purple)" stroke-width="2.5"/>
    <circle cx="640" cy="95" r="6" fill="var(--purple)"/>
    <path d="M575 595 Q700 690 900 625" fill="none" stroke="var(--purple)" stroke-width="2.5"/>
    <circle cx="575" cy="595" r="6" fill="var(--purple)"/>
  </svg>

  <h1 class="headline">
    <span class="q1">Are you the parent of a child age 10–17?</span>
    <span class="q2">Do they worry or overthink negative emotions?</span>
  </h1>

  <p class="intro"><b>Northbridge University</b> researchers are seeking girls <b>age 10-17</b> for a study about brain activity in emotions &amp; decision-making and how they relate to <b>puberty, anxiety &amp; depression.</b></p>

  <section class="involves">
    <h2>Study participation<br>involves:<span class="rule"></span></h2>
    <ul class="steps">
      <li>
        <svg width="36" height="36" viewBox="0 0 36 36" fill="none" stroke="#fff" stroke-width="2"><rect x="4" y="4" width="28" height="18" rx="2"/><circle cx="18" cy="27" r="3"/><path d="M11 34c2-4 12-4 14 0"/></svg>
        <span>One one-hour interview (online or in-person) where your child will discuss their thoughts</span>
      </li>
      <li>
        <svg width="36" height="36" viewBox="0 0 36 36" fill="none" stroke="#fff" stroke-width="2"><circle cx="9" cy="14" r="3"/><circle cx="27" cy="14" r="3"/><path d="M3 30v-6h30v6M12 24h12"/><rect x="13" y="3" width="10" height="7" rx="1"/></svg>
        <span>Online questionnaires (parent and child)</span>
      </li>
      <li>
        <svg width="36" height="36" viewBox="0 0 36 36" fill="none" stroke="#fff" stroke-width="2"><circle cx="18" cy="15" r="12"/><circle cx="18" cy="15" r="6"/><path d="M4 32h28"/></svg>
        <span>One two-hour visit where your child will complete an MRI scan, answer questions about their puberty stage, and have a small hair sample taken to study puberty hormones</span>
      </li>
    </ul>
  </section>

  <section class="eligible">
    <h2>Your child may be eligible if they:</h2>
    <ul class="criteria">
      <li><span class="dot"><svg width="20" height="20" viewBox="0 0 20 20" fill="none" stroke="#fff" stroke-width="1.8"><circle cx="8" cy="7" r="3"/><path d="M2 17c1-5 11-5 12 0"/><circle cx="14" cy="6" r="2"/></svg></span><span>Are age 10-17</span></li>
      <li><span class="dot"><svg width="20" height="20" viewBox="0 0 20 20" fill="none" stroke="#fff" stroke-width="1.8"><circle cx="10" cy="8" r="5"/><path d="M8 15h4M8 18h4"/></svg></span><span>Tend to worry or overthink negative thoughts</span></li>
      <li><span class="dot"><svg width="20" height="20" viewBox="0 0 20 20" fill="none" stroke="#fff" stroke-width="1.8"><rect x="3" y="3" width="14" height="14" rx="1"/><path d="M6 8h8M6 12h8"/></svg></span><span>Have not been diagnosed with psychosis, learning problems, or autism</span></li>
    </ul>
  </section>

  <footer class="contact">
    <p>Interested in participating?<br>Want more information? Please contact us!</p>
    <div class="email">
      <svg width="30" height="22" viewBox="0 0 30 22" fill="none" stroke="#fff" stroke-width="2"><rect x="1" y="1" width="28" height="20" rx="1"/><path d="M1 1l14 11L29 1"/></svg>
      solvestudy@northbridge.edu
    </div>
  </footer>

  <div class="pay">Compensation<br>up to $140</div>
</main>
</body>
</html>
```